Redesign website for small print company

Vindurgata is a small printing company in Iceland mainly servicing Students, schools, etc. We are also doing all kind of other jobs, like business cards, book printing, brochure printing etc. We are also selling books online.
Our website is: www.vindurgata.is
What we are looking for is:
- Web Design (Uncoded - PSD layout only)
- Mobile friendly design, using our current color scheme: Red, green, yellow and light gray.
- Clean simple design
- Simple, light and easy to use.
- More menu Items/drop down
Industry/Entity Type
Digital Printing
Number of Pages Required
5+ page
Requirements
Must have
- Easy navigation
- Designed for mobile
- Current color scheme (see logo)
Nice to have
- Icon based products

```html
<!DOCTYPE html>
<html lang="is">
<head>
<meta charset="utf-8">
<title>Vindurgata – prentþjónusta</title>
<link href="https://fonts.googleapis.com/css2?family=Lato:wght@300;400&family=Roboto:wght@400;500;700&display=swap" rel="stylesheet">
<style>
:root{
  --red:#e8403a;
  --yellow:#fdd10a;
  --ink:#1d1d1d;
  --text:#5a5a5a;
  --grey-bg:#ececec;
  --grey-band:#e9e9e9;
  --line:#d4d4d4;
  --white:#fff;
  --icon:#c9c9c9;
}
*{box-sizing:border-box;margin:0;padding:0}
html,body{width:1200px;height:3364px;overflow:hidden}
body{font-family:"Roboto",Arial,sans-serif;color:var(--ink);background:var(--white);position:relative}
section,header,footer{position:relative;width:1200px}

/* header */
.site-header{height:94px;background:var(--grey-bg)}
.brand{position:absolute;left:78px;top:22px;display:flex;align-items:center;gap:12px}
.brand-mark{width:44px;height:44px;background:var(--red)}
.brand-name{font-weight:700;font-size:35px;line-height:44px;color:var(--ink)}
.main-nav{position:absolute;left:487px;top:36px;display:flex;gap:26px;font-size:17px}
.main-nav a{color:var(--ink);text-decoration:none}
.main-nav a.active{color:var(--red)}
.header-tools{position:absolute;left:895px;top:34px;display:flex;align-items:center;gap:20px;font-size:17px}

/* hero */
.hero{height:583px;background:var(--grey-bg)}
.hero-title{position:absolute;left:78px;top:152px;font-family:"Lato",sans-serif;font-weight:300;font-size:50px;line-height:56px;color:#333}
.hero-text{position:absolute;left:78px;top:272px;width:380px;font-size:14.5px;line-height:24px;color:#444}
.hero-search{position:absolute;left:78px;top:366px;width:433px;height:47px;background:var(--white);display:flex}
.hero-search span{flex:1;padding:15px 16px;font-size:14px;color:#999}
.hero-search b{width:44px;background:var(--red);display:flex;align-items:center;justify-content:center}
.hero-visual{position:absolute;left:572px;top:28px;width:600px;height:520px;background:
  radial-gradient(ellipse 34% 40% at 50% 55%,#f7f5f1 0 60%,rgba(247,245,241,0) 100%),
  radial-gradient(circle at 78% 20%,rgba(228,70,140,.55) 0,rgba(228,70,140,0) 22%),
  radial-gradient(circle at 22% 30%,rgba(246,190,40,.55) 0,rgba(246,190,40,0) 24%),
  radial-gradient(circle at 30% 82%,rgba(140,190,60,.5) 0,rgba(140,190,60,0) 22%),
  radial-gradient(circle at 86% 62%,rgba(70,160,220,.45) 0,rgba(70,160,220,0) 20%),
  radial-gradient(circle at 60% 10%,rgba(240,120,40,.45) 0,rgba(240,120,40,0) 20%)}
.hero-arrow{position:absolute;top:303px}

/* action band */
.action-band{height:81px;background:var(--red)}
.action{position:absolute;top:0;height:81px;display:flex;align-items:center;gap:20px;color:var(--white);font-size:19px}
.action.a1{left:241px}.action.a2{left:518px}.action.a3{left:772px}

/* welcome */
.welcome{height:530px}
.welcome h1{position:absolute;left:78px;top:74px;font-size:45px;font-weight:700;line-height:52px}
.welcome-copy{position:absolute;left:78px;top:150px;width:635px;font-size:14px;line-height:25.5px;color:var(--text)}
.welcome-copy p{margin-bottom:15px}
.welcome-copy p.last{margin-top:26px}
.welcome-visual{position:absolute;left:774px;top:101px;width:283px;height:366px;background:linear-gradient(180deg,#c9c25a 0,#8fb35a 28%,#b8708a 55%,#c24a6c 100%)}

/* subscribe */
.subscribe{height:222px;background:var(--grey-band)}
.subscribe-person{position:absolute;left:101px;top:14px;width:190px;height:208px;border-radius:80px 80px 0 0;background:linear-gradient(180deg,#d8c2ae 0,#e9ddd2 35%,#fbfbfb 55%,#f0f0f0 100%)}
.subscribe h2{position:absolute;left:303px;top:52px;font-size:26px;font-weight:700}
.subscribe p{position:absolute;left:303px;top:99px;font-size:13.5px;color:var(--text)}
.subscribe-input{position:absolute;left:303px;top:125px;width:518px;height:47px;background:var(--white);padding:15px 16px;font-size:14px;color:#888}
.subscribe-btn{position:absolute;left:832px;top:125px;width:198px;height:47px;background:var(--red);color:var(--white);font-weight:700;font-size:17px;display:flex;align-items:center;justify-content:center}

/* categories */
.categories{height:728px}
.section-title{position:absolute;left:0;width:1200px;text-align:center;font-size:45px;font-weight:700;line-height:52px}
.categories .section-title{top:56px}
.category-grid{position:absolute;left:78px;top:139px;display:grid;grid-template-columns:repeat(3,332px);grid-template-rows:repeat(2,228px);gap:23px 24px}
.category{position:relative;overflow:hidden;background:#efefef}
.category.featured{background:linear-gradient(135deg,#e8e4df,#f6f3f0)}
.featured-shape{position:absolute;inset:0}
.category-label{position:absolute;left:22px;top:42px;color:var(--white);font-weight:700;font-size:21px;z-index:1}
.category-tools{position:absolute;left:216px;top:145px;display:flex;gap:12px;z-index:1}
.category-tools span{width:42px;height:42px;border:2px solid var(--white);border-radius:50%;display:flex;align-items:center;justify-content:center}
.cat-2{background:radial-gradient(ellipse 32% 55% at 52% 50%,#fafafa 0 70%,rgba(250,250,250,0) 100%),linear-gradient(180deg,#eeede9,#d7d3cc)}
.cat-3{background:radial-gradient(ellipse 45% 45% at 60% 55%,rgba(70,110,170,.55),rgba(70,110,170,0)),radial-gradient(ellipse 30% 30% at 40% 70%,rgba(230,140,50,.45),rgba(230,140,50,0)),#f1f1f1}
.cat-4{background:radial-gradient(ellipse 45% 50% at 50% 55%,rgba(225,110,70,.6),rgba(225,110,70,0)),radial-gradient(ellipse 25% 30% at 30% 30%,rgba(220,70,140,.45),rgba(220,70,140,0)),#f1f1f1}
.cat-5{background:radial-gradient(ellipse 55% 35% at 50% 65%,rgba(30,30,30,.85),rgba(30,30,30,0)),#ececec}
.cat-6{background:radial-gradient(ellipse 30% 45% at 55% 55%,#fbfbfb 0 70%,rgba(251,251,251,0) 100%),radial-gradient(ellipse 40% 30% at 60% 25%,rgba(220,80,150,.5),rgba(220,80,150,0)),#ececec}

/* promo */
.promo{height:240px;background:var(--red)}
.promo-book{position:absolute;left:253px;top:-67px;width:193px;height:263px;background:linear-gradient(180deg,#8c6a34 0,#e9c53a 22%,#e3be3a 80%,#8c6a34 100%);box-shadow:4px 6px 12px rgba(0,0,0,.3)}
.price-badge{position:absolute;left:375px;top:-27px;width:89px;height:89px;border-radius:50%;background:var(--yellow);display:flex;flex-direction:column;align-items:center;justify-content:center;font-weight:700;font-size:18px;line-height:20px}
.price-badge small{font-size:14px}
.promo-title{position:absolute;left:491px;top:48px;color:var(--white);font-size:23px;font-weight:400;line-height:34px;letter-spacing:1.2px;text-transform:uppercase}
.promo-btn{position:absolute;left:491px;top:126px;width:200px;height:54px;border:2px solid var(--white);color:var(--white);font-weight:700;font-size:17px;display:flex;align-items:center;justify-content:center}

/* products */
.products{height:415px}
.products .section-title{top:56px}
.product-row{position:absolute;left:80px;top:142px;display:flex;gap:31px}
.product{width:155px;height:211px;border-radius:14px;display:flex;flex-direction:column;align-items:center;justify-content:flex-end;padding-bottom:28px;gap:30px;font-weight:700;font-size:19px}
.product.active{background:var(--yellow)}
.carousel-arrow{position:absolute;top:230px}

/* contact + footer */
.contact-band{height:241px;background:var(--grey-band)}
.contact-band h2{position:absolute;left:0;top:64px;width:1200px;text-align:center;font-size:38px;font-weight:700}
.contact-btn{position:absolute;left:453px;top:128px;width:294px;height:48px;background:var(--red);color:var(--white);font-weight:700;font-size:19px;display:flex;align-items:center;justify-content:center}
.site-footer{height:230px;background:var(--grey-band)}
.footer-rule{position:absolute;left:78px;right:78px;top:0;border-top:1px solid var(--line)}
.site-footer .brand{top:40px}
.copyright{position:absolute;left:101px;top:106px;font-size:14px;color:#444}
.cards{position:absolute;left:195px;top:140px;display:flex;gap:12px}
.cards span{width:50px;height:38px;border-radius:4px;background:#d4d4d4}
.footer-col{position:absolute;top:42px;font-size:15px;line-height:32px;color:#444}
.footer-col h3{font-size:18px;font-weight:700;color:var(--ink);line-height:26px;margin-bottom:4px}
.social{width:45px;height:45px;background:var(--red);margin-top:8px}
</style>
</head>
<body>
<header class="site-header">
  <div class="brand"><span class="brand-mark"></span><span class="brand-name">VINDURGATA</span></div>
  <nav class="main-nav"><a class="active" href="#">Heim</a><a href="#">Pjonusta</a><a href="#">Skil a Verkum</a><a href="#">Um okkur</a></nav>
  <div class="header-tools">
    <span>Simi: 555 0142</span>
    <svg width="22" height="22" viewBox="0 0 24 24" fill="none" stroke="#e8403a" stroke-width="2"><path d="M6 18V11a6 6 0 0 1 12 0v7H6zM4 18h16M10 21h4"/></svg>
    <svg width="22" height="22" viewBox="0 0 24 24" fill="none" stroke="#e8403a" stroke-width="2.4"><circle cx="10" cy="10" r="6"/><path d="M15 15l6 6"/></svg>
    <svg width="26" height="20" viewBox="0 0 26 20"><rect width="26" height="20" fill="#1d4fa0"/><path d="M0 10h26M9 0v20" stroke="#fff" stroke-width="6"/><path d="M0 10h26M9 0v20" stroke="#d8322d" stroke-width="3"/></svg>
  </div>
</header>

<section class="hero">
  <svg class="hero-arrow" style="left:28px" width="20" height="50" viewBox="0 0 20 50" fill="none" stroke="#999" stroke-width="2"><path d="M18 2L2 25l16 23"/></svg>
  <svg class="hero-arrow" style="left:1152px" width="20" height="50" viewBox="0 0 20 50" fill="none" stroke="#999" stroke-width="2"><path d="M2 2l16 23L2 48"/></svg>
  <h2 class="hero-title">Vio Prentum<br>Skyrslur</h2>
  <p class="hero-text">Við erum líka að gera alls konar önnur störf, eins og nafnspjöld, bók prentun, bækling prentun osfrv. Við erum líka að selja bækur á netinu.</p>
  <div class="hero-search"><span>Suche...</span><b><svg width="20" height="20" viewBox="0 0 24 24" fill="none" stroke="#fff" stroke-width="2.6"><circle cx="10" cy="10" r="6"/><path d="M15 15l6 6"/></svg></b></div>
  <div class="hero-visual" role="img" aria-label="Prentaðar skýrslur og möppur umkringdar litríkum málningarslettum"></div>
</section>

<section class="action-band">
  <div class="action a1"><svg width="58" height="46" viewBox="0 0 58 46"><rect x="2" y="10" width="54" height="34" rx="4" fill="#fdd10a"/><path d="M21 10V4h16v6" fill="none" stroke="#fdd10a" stroke-width="4"/><path d="M2 22h54" stroke="#e8403a" stroke-width="2"/></svg>SEND A VERK</div>
  <div class="action a2"><svg width="52" height="52" viewBox="0 0 52 52"><circle cx="26" cy="26" r="24" fill="#fdd10a"/><circle cx="18" cy="16" r="5" fill="#e8403a"/><circle cx="32" cy="14" r="5" fill="#e8403a"/><circle cx="38" cy="27" r="5" fill="#e8403a"/><circle cx="16" cy="32" r="5" fill="#e8403a"/></svg>HANNA VERK</div>
  <div class="action a3"><svg width="52" height="52" viewBox="0 0 52 52"><circle cx="26" cy="26" r="24" fill="#fdd10a"/><path d="M19 20a7 7 0 1 1 10 6c-3 2-3 3-3 6" fill="none" stroke="#e8403a" stroke-width="4"/><circle cx="26" cy="39" r="3" fill="#e8403a"/></svg>FA TILBOD</div>
</section>

<section class="welcome">
  <h1>Velkomin í Vindurgata</h1>
  <div class="welcome-copy">
    <p>Vindurgata er fyrirtæki staðsett á háskólasvæðinu sem hefur sérhæft sig í að þjónusta skólafólk, ásamt því að sinna allri almennri prentun fyrir almenning.</p>
    <p>Vindurgata gefur út greinasöfn og frumsamdar kennslubækur fyrir námskeið, prentar lokaritgerðir fyrir nema, auk þess að vinna við ótalinn fjölda smærri verka fyrir nemendur, kennara og stofnanir. Má þar nefna bæklinga, skýrslur, spurningalista, nafnspjöld, bækur, OCR skönnun og fleira.</p>
    <p>Vindurgata er umhverfisvottuð prentsmiðja, Laufið er opinbert umhverfismerki Norðurlandanna, sem hefur skapað sér fótfestu hér á landi og er þekkt meðal neytenda.</p>
    <p class="last">Vindurgata er staðsett á horninu á Lindargötu og Hólagötu. (gengið inn Hólagötumegin)</p>
  </div>
  <div class="welcome-visual" role="img" aria-label="Litrík ljósmynd af prentsmiðjunni að innan"></div>
</section>

<section class="subscribe">
  <div class="subscribe-person" role="img" aria-label="Ljósmynd af ungum manni með spjaldtölvu"></div>
  <h2>biðja um spurningu ?</h2>
  <p>Lorem Ipsum is simply dummy text of the printing and typesetting industry. Lorem</p>
  <div class="subscribe-input">Sláðu inn tölvupóst</div>
  <div class="subscribe-btn">gerast áskrifandi</div>
</section>

<section class="categories">
  <h2 class="section-title">Vöruflokkar</h2>
  <div class="category-grid">
    <div class="category featured" role="img" aria-label="Innbundnar ritgerðir">
      <svg class="featured-shape" width="332" height="228" viewBox="0 0 332 228"><path d="M0 0h176C120 40 96 110 110 228H0z" fill="#e8403a" opacity=".88"/><circle cx="300" cy="240" r="150" fill="#e8403a"/></svg>
      <span class="category-label">Ritgerðir</span>
      <div class="category-tools">
        <span><svg width="18" height="18" viewBox="0 0 24 24" fill="none" stroke="#fff" stroke-width="2"><path d="M6 18V11a6 6 0 0 1 12 0v7H6zM4 18h16"/></svg></span>
        <span><svg width="18" height="18" viewBox="0 0 24 24" fill="none" stroke="#fff" stroke-width="2.4"><circle cx="10" cy="10" r="6"/><path d="M15 15l6 6"/></svg></span>
      </div>
    </div>
    <div class="category cat-2" role="img" aria-label="Jólakort á borði"></div>
    <div class="category cat-3" role="img" aria-label="Prentaðir bæklingar"></div>
    <div class="category cat-4" role="img" aria-label="Myndskreyttar barnabækur"></div>
    <div class="category cat-5" role="img" aria-label="Prentuð veggspjöld í rúllum"></div>
    <div class="category cat-6" role="img" aria-label="Kennslubók í tölfræði"></div>
  </div>
</section>

<section class="promo">
  <div class="promo-book" role="img" aria-label="Bókarkápa"></div>
  <div class="price-badge">5.450<small>kr</small></div>
  <h2 class="promo-title">The Craft of Clear<br>Academic Writing</h2>
  <div class="promo-btn">bæta við í körfu</div>
</section>

<section class="products">
  <h2 class="section-title">vörur</h2>
  <svg class="carousel-arrow" style="left:28px" width="14" height="34" viewBox="0 0 14 34" fill="none" stroke="#bbb" stroke-width="2"><path d="M12 2L2 17l10 15"/></svg>
  <svg class="carousel-arrow" style="left:1156px" width="14" height="34" viewBox="0 0 14 34" fill="none" stroke="#bbb" stroke-width="2"><path d="M2 2l10 15L2 32"/></svg>
  <div class="product-row">
    <div class="product"><svg width="76" height="84" viewBox="0 0 76 84"><rect x="10" y="4" width="58" height="76" rx="4" fill="#c9c9c9"/><rect x="4" y="8" width="10" height="72" rx="3" fill="#b3b3b3"/></svg>bækur</div>
    <div class="product active"><svg width="100" height="90" viewBox="0 0 100 90"><rect x="4" y="10" width="92" height="76" fill="#111"/><rect x="22" y="2" width="6" height="16" fill="#111"/><rect x="72" y="2" width="6" height="16" fill="#111"/><g fill="#fdd10a"><rect x="12" y="30" width="10" height="9"/><rect x="28" y="30" width="10" height="9"/><rect x="44" y="30" width="10" height="9"/><rect x="60" y="30" width="10" height="9"/><rect x="76" y="30" width="10" height="9"/><rect x="12" y="47" width="10" height="9"/><rect x="28" y="47" width="10" height="9"/><rect x="44" y="47" width="10" height="9"/><rect x="60" y="47" width="10" height="9"/><rect x="76" y="47" width="10" height="9"/><rect x="12" y="64" width="10" height="9"/><rect x="28" y="64" width="10" height="9"/><rect x="44" y="64" width="10" height="9"/><rect x="60" y="64" width="10" height="9"/></g></svg>dagatal</div>
    <div class="product"><svg width="70" height="84" viewBox="0 0 70 84"><path d="M6 8l28 6v66L6 74z" fill="#c9c9c9"/><path d="M34 14l30-8v66l-30 8z" fill="#b3b3b3"/><path d="M40 26l18-5M40 36l18-5M40 46l18-5" stroke="#fff" stroke-width="3"/></svg>kennslubók</div>
    <div class="product"><svg width="120" height="84" viewBox="0 0 120 84"><rect x="4" y="6" width="112" height="74" rx="8" fill="none" stroke="#c9c9c9" stroke-width="5"/><circle cx="36" cy="34" r="11" fill="#c9c9c9"/><path d="M18 64c2-14 34-14 36 0z" fill="#c9c9c9"/><text x="66" y="58" font-family="Roboto,sans-serif" font-size="38" fill="#c9c9c9">@</text></svg>nafnspjald</div>
    <div class="product"><svg width="66" height="86" viewBox="0 0 66 86"><rect x="3" y="3" width="60" height="80" fill="none" stroke="#c9c9c9" stroke-width="4"/><g stroke="#c9c9c9" stroke-width="3"><path d="M13 16h40M13 24h40M13 32h40M13 40h40M13 48h40M13 56h40M13 64h40M13 72h40"/></g></svg>Kennslubækur</div>
    <div class="product"><svg width="66" height="86" viewBox="0 0 66 86"><path d="M3 3h44l16 16v64H3z" fill="#c9c9c9"/><path d="M47 3v16h16" fill="#e2e2e2"/><text x="12" y="34" font-family="Roboto,sans-serif" font-size="20" font-weight="700" fill="#fff">AD</text><path d="M10 70l14-22 10 14 8-8 14 16z" fill="#fff"/></svg>Veggspjald</div>
  </div>
</section>

<section class="contact-band">
  <h2>Hafa Spurning ?</h2>
  <div class="contact-btn">Hafðu samband við okkur</div>
</section>

<footer class="site-footer">
  <div class="footer-rule"></div>
  <div class="brand"><span class="brand-mark"></span><span class="brand-name">VINDURGATA</span></div>
  <p class="copyright">©Vindurgata - 2018 Allur réttur svaraður</p>
  <div class="cards"><span></span><span></span></div>
  <div class="footer-col" style="left:485px"><h3>Veftré</h3>Heim<br>Pjonusta<br>Skil a Verkum<br>Um okkur</div>
  <div class="footer-col" style="left:691px"><h3>Hafðu samband</h3>verk@vindurgata.is<br>Man - Fos : 9-17<br>Simi: 555 0142</div>
  <div class="footer-col" style="left:915px"><h3>Fylgdu okkur á</h3><div class="social"></div></div>
</footer>
</body>
</html>
```